Business Cards for a law firm

Business cards for our law firm. Use our silhoette logo and OAK PARTNERS - check our website (www.oakpartners.example)

Contact Information for Business Card

our silhouette logo, OAK PARTNERS, 800-555-0147, Dorian Pemberton, dorian@oakpartners.example

Requirements
Must have
• our silhouette logo, OAK PARTNERS, 800-555-0147, Dorian Pemberton, dorian@oakpartners.example

```html
<!DOCTYPE html>
<html lang="en">
<head>
<meta charset="UTF-8">
<title>Oak Partners — Business Card</title>
<link href="https://fonts.googleapis.com/css2?family=Tenor+Sans&family=Montserrat:wght@400;500;700&display=swap" rel="stylesheet">
<style>
  :root {
    --navy: #24336a;
    --navy-soft: #3a4a82;
    --paper: #ffffff;
    --backdrop: #e0e5e7;
  }
  * { margin: 0; padding: 0; box-sizing: border-box; }
  html, body {
    width: 1200px;
    height: 960px;
    overflow: hidden;
    background: var(--backdrop);
  }
  .sheet {
    position: relative;
    width: 1200px;
    height: 960px;
  }
  .card {
    position: absolute;
    left: 247px;
    width: 706px;
    height: 404px;
  }
  .card--front {
    top: 59px;
    background: var(--navy);
  }
  .card--back {
    top: 500px;
    background: var(--paper);
  }

  /* Front: logo area + firm name */
  .logo-mark {
    position: absolute;
    left: 106px;
    top: 119px;
    width: 108px;
    height: 163px;
    background: var(--navy-soft);
  }
  .wordmark {
    position: absolute;
    left: 227px;
    top: 139px;
    font-family: "Tenor Sans", sans-serif;
    font-weight: 400;
    color: var(--paper);
    line-height: 49px;
    white-space: nowrap;
  }
  .wordmark__line {
    display: block;
    font-size: 60px;
    letter-spacing: 3px;
  }

  /* Back: person + contact */
  .person {
    position: absolute;
    left: 26px;
    top: 184px;
    font-family: "Montserrat", sans-serif;
    font-size: 25.5px;
    color: var(--navy);
    letter-spacing: 0.5px;
    white-space: nowrap;
  }
  .person__first { font-weight: 700; }
  .person__last { font-weight: 400; }

  .divider {
    position: absolute;
    left: 351px;
    top: 140px;
    width: 1px;
    height: 120px;
    background: var(--navy);
  }

  .contact {
    position: absolute;
    left: 386px;
    top: 169px;
    list-style: none;
    font-family: "Montserrat", sans-serif;
    color: var(--navy);
  }
  .contact__item {
    display: flex;
    align-items: center;
    gap: 11px;
    white-space: nowrap;
  }
  .contact__item--phone { font-size: 18.5px; font-weight: 500; letter-spacing: 0.3px; height: 24px; }
  .contact__item--email { font-size: 13.5px; font-weight: 500; letter-spacing: 0.8px; margin-top: 5px; height: 20px; }
  .contact__icon { width: 14px; height: 14px; flex: none; }

  .website {
    position: absolute;
    left: 0;
    right: 0;
    top: 342px;
    text-align: center;
    font-family: "Montserrat", sans-serif;
    font-weight: 500;
    font-size: 13px;
    letter-spacing: 0.8px;
    color: var(--navy);
  }
</style>
</head>
<body>
<main class="sheet">
  <section class="card card--front" aria-label="Card front">
    <div class="logo-mark" role="img" aria-label="Firm silhouette logo"></div>
    <h1 class="wordmark">
      <span class="wordmark__line">OAK</span>
      <span class="wordmark__line">PARTNERS</span>
    </h1>
  </section>

  <section class="card card--back" aria-label="Card back">
    <p class="person">
      <span class="person__first">DORIAN</span>
      <span class="person__last">PEMBERTON</span>
    </p>
    <div class="divider"></div>
    <ul class="contact">
      <li class="contact__item contact__item--phone">
        <svg class="contact__icon" viewBox="0 0 24 24" aria-hidden="true">
          <path fill="#24336a" d="M6.6 10.8a15.1 15.1 0 0 0 6.6 6.6l2.2-2.2a1 1 0 0 1 1-.25 11.4 11.4 0 0 0 3.6.57 1 1 0 0 1 1 1V20a1 1 0 0 1-1 1A17 17 0 0 1 3 4a1 1 0 0 1 1-1h3.5a1 1 0 0 1 1 1c0 1.25.2 2.45.57 3.57a1 1 0 0 1-.25 1z"/>
        </svg>
        800-555-0147
      </li>
      <li class="contact__item contact__item--email">
        <svg class="contact__icon" viewBox="0 0 24 24" aria-hidden="true">
          <rect x="2" y="6" width="20" height="14" rx="1.5" fill="#24336a"/>
          <path d="M3 7l9 7 9-7" fill="none" stroke="#ffffff" stroke-width="1.6"/>
        </svg>
        DORIAN@OAKPARTNERS.EXAMPLE
      </li>
    </ul>
    <p class="website">WWW.OAKPARTNERS.EXAMPLE</p>
  </section>
</main>
</body>
</html>
```